Brickfield real estate investment company needs a poster design

We would like a poster design size 18 x 24.
Poster wording -
I WANT TO BUY YOUR ( finish with logo) logo uploaded
website- www.brickfield.example
phone # 555-218-7043 ( color red for the phone number)
we would like to see the poster on 2 different backgrounds
Yellow background
White background
horizontal

```html
<!DOCTYPE html>
<html lang="en">
<head>
<meta charset="utf-8">
<title>Brickfield — I Want To Buy Your House</title>
<link rel="stylesheet" href="https://fonts.googleapis.com/css2?family=Montserrat:wght@600;800;900&family=Roboto:wght@500&display=swap">
<style>
  :root {
    --sign-yellow: #fdeb05;
    --ink-black: #000000;
    --sign-red: #e21f26;
    --paper-white: #ffffff;
  }
  html, body {
    margin: 0;
    padding: 0;
    width: 1200px;
    height: 900px;
    overflow: hidden;
    background: var(--sign-yellow);
  }
  .poster {
    display: block;
    width: 1200px;
    height: 900px;
  }
  .headline-main {
    font-family: "Montserrat", sans-serif;
    font-weight: 900;
    font-size: 300px;
    fill: var(--ink-black);
  }
  .headline-sub {
    font-family: "Montserrat", sans-serif;
    font-weight: 800;
    font-size: 188px;
    fill: var(--paper-white);
  }
  .brand-name {
    font-family: "Montserrat", sans-serif;
    font-weight: 800;
    font-size: 126px;
    fill: var(--ink-black);
  }
  .brand-site {
    font-family: "Montserrat", sans-serif;
    font-weight: 600;
    font-size: 44px;
    fill: var(--ink-black);
  }
  .phone-number {
    font-family: "Roboto", sans-serif;
    font-weight: 500;
    font-size: 177px;
    fill: var(--paper-white);
  }
  .wave-black { fill: var(--ink-black); }
  .wave-red { fill: var(--sign-red); }
  .phone-badge { fill: var(--sign-yellow); }
  .phone-icon { fill: var(--ink-black); }
</style>
</head>
<body>
<svg class="poster" viewBox="0 0 1200 900" xmlns="http://www.w3.org/2000/svg">
  <rect width="1200" height="900" fill="var(--sign-yellow)"/>

  <text class="headline-main" x="26" y="212" textLength="1152" lengthAdjust="spacingAndGlyphs">I WANT</text>
  <text class="headline-sub" x="28" y="372" textLength="1136" lengthAdjust="spacingAndGlyphs">TO BUY YOUR</text>

  <text class="brand-name" x="342" y="552" textLength="820" lengthAdjust="spacingAndGlyphs">BRICKFIELD</text>
  <text class="brand-site" x="1160" y="607" text-anchor="end">www.brickfield.example</text>

  <path class="wave-black" d="M0,696 C120,640 240,612 344,610 C500,604 620,630 720,652 C860,680 1000,700 1200,652 L1200,900 L0,900 Z"/>
  <path class="wave-red" d="M0,832 C100,740 250,660 400,652 C520,646 620,664 720,676 C830,690 950,712 1200,680 L1200,900 L0,900 Z"/>

  <circle class="phone-badge" cx="124" cy="780" r="78"/>
  <path class="phone-icon" d="M94,732 L102,726 Q105,724 107,727 L120,746 Q122,749 119,751 L112,756 Q110,758 111,762 Q118,790 138,805 Q141,807 143,805 L149,800 Q152,798 154,801 L166,819 Q168,822 165,825 L158,830 Q146,836 128,824 Q102,806 90,776 Q82,750 90,736 Z"/>

  <text class="phone-number" x="228" y="854" textLength="932" lengthAdjust="spacingAndGlyphs">555-218-7043</text>
</svg>
</body>
</html>
```